QRV Advisors needs a web site

We need a web site for www.qrvadvisors-example.com. QRV is a mergers and acquisition consulting company that focuses our buyer and seller services on logistics companies. We help put companies together, and help with legal and financial due diligence. We want the web site to express our service and show the logistics components. We want personalized images versus pictures of trucks and airplanes.

Our new logo uses Burgandy and grey colors. Image attached. We are not in to bold, big letters...classy, artistic, low key preferred. Confidentiality, experience, professional are what we want to express on the site.

All we expect for the first part of this project is a home page, and one subpage.  We are budgeting other funds for the technical aspects of the web site

Reason: All that I'm seeing so far is trucks, forklifts and planes. We are a legal mergers and acquisitions firm that focus on logistics. I like some of the images to say logistics, but really want it say legal, financial, and putting companies together. Will pay extra for the sub page if someone can impress us with a home page.

Reason: Swamped with another project at the moment...will work on this over the weekend and provide designer feedback and select final design by Tuesday

```html
<!DOCTYPE html>
<html lang="en">
<head>
<meta charset="utf-8">
<title>QRV Advisors – Mergers &amp; Acquisitions Consulting Services</title>
<link rel="stylesheet" href="https://fonts.googleapis.com/css2?family=Open+Sans:wght@300;400;600;700&display=swap">
<style>
:root{
  --burgundy:#9b0f35;
  --burgundy-dark:#7c0a29;
  --ink:#333333;
  --grey:#666666;
  --muted:#a9a9a9;
  --topbar:#4a4a4a;
  --header:#f4f4f4;
  --line:#dddddd;
  --sky:#1d9fd1;
  --sky-deep:#0f86b8;
  --footer:#1c1c1c;
  --footer-base:#0e0e0e;
  --white:#ffffff;
}
*{box-sizing:border-box;margin:0;padding:0}
html,body{width:1200px;height:2256px;overflow:hidden}
body{position:relative;font-family:"Open Sans",Arial,sans-serif;color:var(--ink);background:var(--white)}
.abs{position:absolute}

.top-bar{left:0;top:0;width:1200px;height:33px;background:var(--topbar)}
.top-links{left:111px;top:0;height:33px;display:flex;gap:18px;align-items:center}
.top-links a{color:#e8e8e8;font-size:10.5px;text-decoration:none;text-transform:uppercase}
.top-social{left:957px;top:6px;display:flex;gap:6px}
.top-social span{width:21px;height:21px;border-radius:50%;background:#6e6e6e;display:block}

.site-header{left:0;top:33px;width:1200px;height:167px;background:var(--header)}
.brand{left:112px;top:56px}
.brand-name{font-size:58px;font-weight:400;letter-spacing:8px;color:#555555;line-height:1}
.brand-tag{font-size:9.5px;color:var(--burgundy);margin-top:4px}
.search{left:850px;top:80px;width:236px;height:32px;border:1px solid var(--line);background:var(--white);border-radius:3px;font-size:13px;color:#c2c2c2;padding:7px 10px}
.search svg{position:absolute;right:9px;top:7px}

.main-nav{left:110px;top:152px;width:976px;height:48px;display:flex}
.main-nav a{flex:1;display:flex;align-items:center;justify-content:center;font-size:15.5px;color:#555;text-decoration:none;background:#f0f0f0;border-right:1px solid var(--line);border-top:1px solid #e6e6e6}
.main-nav a.active{background:var(--white);color:var(--burgundy);font-weight:700;font-size:15px;text-transform:uppercase}

.hero{left:0;top:237px;width:1200px;height:521px;background:linear-gradient(90deg,#b4865a 0%,#c99a6c 30%,#a9a7ab 55%,#e2d2bd 75%,#cdb79e 100%)}
.hero-box{left:110px;top:393px;width:444px;height:239px;background:rgba(10,10,10,.82)}
.hero-title{position:absolute;left:0;top:0;width:444px;height:63px;background:#3a3a3a}
.hero-title .red{position:absolute;left:0;top:0;width:242px;height:63px;background:var(--burgundy);clip-path:polygon(0 0,100% 0,92% 100%,0 100%)}
.hero-title h1{position:absolute;left:14px;top:9px;font-size:35px;font-weight:300;color:var(--white);white-space:nowrap}
.hero-title h1 b{font-weight:700}
.hero-box p{position:absolute;left:14px;top:76px;width:416px;font-size:12.8px;line-height:19.5px;color:#eee}
.btn{display:inline-block;background:var(--burgundy);color:var(--white);font-size:14px;text-decoration:none;border-radius:3px;border-bottom:2px solid var(--burgundy-dark);text-align:center}
.hero-box .btn{position:absolute;left:14px;top:194px;width:109px;height:32px;line-height:31px}
.hero-shadow{left:40px;top:758px;width:1120px;height:22px;background:radial-gradient(ellipse at top,rgba(0,0,0,.13),rgba(0,0,0,0) 70%)}

.service{top:833px;height:292px;text-align:center}
.service.featured{background:#ececec;box-shadow:0 8px 10px -6px rgba(0,0,0,.2)}
.service svg{display:block;margin:0 auto}
.service h2{font-size:18px;font-weight:400;color:#222;margin-top:8px}
.service.featured h2{color:var(--burgundy)}
.service p{font-size:12.4px;line-height:20px;color:var(--muted);margin:6px auto 0;width:300px}
.service .btn{width:109px;height:33px;line-height:32px;margin-top:20px;font-size:13.5px}

.testimonials{left:0;top:1170px;width:1200px;height:353px;background:linear-gradient(180deg,var(--sky) 0%,var(--sky-deep) 100%);text-align:center;color:var(--white)}
.testimonials h2{position:absolute;left:0;top:26px;width:1200px;font-size:31px;font-weight:400}
.avatar{left:541px;top:99px;width:112px;height:112px;border-radius:50%;border:3px solid var(--white);background:linear-gradient(160deg,#e8cf9a,#3b5b63)}
.avatar-pointer{left:589px;top:211px;width:0;height:0;border-left:9px solid transparent;border-right:9px solid transparent;border-top:9px solid var(--white)}
.testimonials h3{position:absolute;left:0;top:227px;width:1200px;font-size:20px;font-weight:600}
.testimonials p{position:absolute;left:120px;top:263px;width:960px;font-size:12.8px;line-height:20px}

.lower{left:0;top:1523px;width:1200px;height:435px;background:#f7f7f7}
.contact-box{left:110px;top:1580px;width:302px;height:322px;background:#e7e7e7;padding:10px 11px}
.contact-box h2{font-size:29px;font-weight:600;color:var(--burgundy)}
.contact-box p{font-size:11px;line-height:13px;color:#888;margin-top:2px}
.field{background:var(--white);border:1px solid #ddd;border-radius:3px;height:32px;font-size:11.5px;color:#888;padding:8px 9px;margin-top:8px}
.field.first{margin-top:12px}
.field.msg{height:80px}
.form-foot{position:absolute;left:11px;top:279px;width:280px;display:flex;align-items:center;justify-content:space-between}
.form-foot label{font-size:11px;color:#777;display:flex;align-items:center;gap:4px}
.form-foot i{display:block;width:10px;height:10px;border:1px solid #999;background:var(--white)}
.form-foot .btn{width:108px;height:33px;line-height:32px;font-size:15px}

.pros-title{left:462px;top:1571px;font-size:26px;font-weight:400;color:#777}
.pro-photo{left:468px;width:171px;height:131px}
.pro-text{left:648px;width:440px;font-size:12.8px;line-height:20px;color:#888}

.site-footer{left:0;top:1958px;width:1200px;height:255px;background:var(--footer);color:#9c9c9c}
.foot-brand{left:111px;top:36px}
.foot-brand .brand-name{color:var(--white);font-size:52px}
.foot-brand .brand-tag{color:#ccc;margin-top:3px}
.foot-about{left:111px;top:110px;width:310px;font-size:12.8px;line-height:20px}
.foot-col h4{font-size:15.5px;font-weight:400;color:var(--white);margin-bottom:22px}
.foot-col ul{list-style:none;font-size:14px;line-height:20px}
.foot-col li.active{color:var(--burgundy)}
.foot-contact{font-size:13.3px;line-height:22px}
.foot-social{display:flex;gap:6px}
.foot-social span{width:27px;height:27px;border-radius:50%;background:#8a8a8a;display:block}
.copyright{left:0;top:2213px;width:1200px;height:43px;background:var(--footer-base);color:var(--white);font-size:12px;text-align:center;line-height:43px}
</style>
</head>
<body>

<div class="abs top-bar"></div>
<nav class="abs top-links"><a href="#">Find a Location</a><a href="#">Contact Us</a><a href="#">About Us</a></nav>
<div class="abs top-social"><span></span><span></span><span></span><span></span><span></span></div>

<header class="abs site-header"></header>
<div class="abs brand"><div class="brand-name">QRV</div><div class="brand-tag">Mergers &amp; Acquisitions Consulting Services</div></div>
<div class="abs search">Search
  <svg width="18" height="18" viewBox="0 0 18 18"><circle cx="7.5" cy="7.5" r="5.5" fill="none" stroke="#aaa" stroke-width="1.6"/><line x1="11.5" y1="11.5" x2="16" y2="16" stroke="#aaa" stroke-width="1.8"/></svg>
</div>
<nav class="abs main-nav">
  <a href="#" class="active">Home</a><a href="#">About Us</a><a href="#">Services</a><a href="#">Careers</a><a href="#">Contact Us</a>
</nav>

<section class="abs hero" role="img" aria-label="Warehouse with stacked cardboard boxes and a consultant holding a clipboard"></section>
<div class="abs hero-box">
  <div class="hero-title"><div class="red"></div><h1>Trusted Merger <b>Solutions</b></h1></div>
  <p>Lorem ipsum dolor sit amet, consectetur adipisicing elit, sed do eius-mod tempor incididunt ut labore et dolore magna aliqua. Ut enim ad minim veniam, quis nostrud exercitation ullamco laboris nisi ut aliquip ex ea commodo consequat. Duis aute irure dolor in repre-henderit in voluptate velit esse cillum dolore eu fugiat nulla paria-tur.</p>
  <a href="#" class="btn">Read More</a>
</div>
<div class="abs hero-shadow"></div>

<article class="abs service featured" style="left:110px;width:320px;padding-top:12px">
  <svg width="70" height="80" viewBox="0 0 70 80" fill="var(--burgundy)">
    <rect x="12" y="4" width="46" height="30" rx="4"/>
    <rect x="17" y="9" width="36" height="18" rx="2" fill="#ececec"/>
    <rect x="4" y="16" width="6" height="12" rx="1"/><rect x="60" y="16" width="6" height="12" rx="1"/>
    <rect x="8" y="36" width="54" height="22" rx="3"/>
    <rect x="16" y="42" width="38" height="3" fill="#ececec"/><rect x="16" y="48" width="38" height="3" fill="#ececec"/>
    <circle cx="14" cy="47" r="3" fill="#ececec"/><circle cx="56" cy="47" r="3" fill="#ececec"/>
    <rect x="4" y="60" width="62" height="6" rx="1"/>
    <rect x="10" y="68" width="12" height="10" rx="2"/><rect x="48" y="68" width="12" height="10" rx="2"/>
  </svg>
  <h2>Logistics</h2>
  <p>Lorem ipsum dolor sit amet, consectetur adipisicing elit, sed do eiusmod tempor incididunt ut labore et dolore magna aliqua. Ut enim ad minim veniam, quis nostrud.</p>
  <a href="#" class="btn">Read More</a>
</article>
<article class="abs service" style="left:450px;width:300px;padding-top:18px">
  <svg width="54" height="68" viewBox="0 0 54 68" fill="none" stroke="#3a3a3a" stroke-width="4">
    <rect x="4" y="8" width="46" height="57" rx="3"/>
    <rect x="17" y="3" width="20" height="10" rx="2" fill="#3a3a3a"/>
    <polyline points="11,25 14,28 19,22" stroke-width="2.6"/><line x1="24" y1="25" x2="42" y2="25" stroke-width="3"/>
    <polyline points="11,38 14,41 19,35" stroke-width="2.6"/><line x1="24" y1="38" x2="42" y2="38" stroke-width="3"/>
    <polyline points="11,51 14,54 19,48" stroke-width="2.6"/><line x1="24" y1="51" x2="42" y2="51" stroke-width="3"/>
  </svg>
  <h2>Legal And Financial</h2>
  <p>Lorem ipsum dolor sit amet, consectetur adipisicing elit, sed do eiusmod tempor incididunt ut labore et dolore magna aliqua. Ut enim ad minim veniam, quis nostrud.</p>
  <a href="#" class="btn">Read More</a>
</article>
<article class="abs service" style="left:776px;width:304px;padding-top:18px">
  <svg width="74" height="74" viewBox="0 0 74 74" fill="#3a3a3a">
    <path d="M22 20 a15 15 0 0 1 30 0 Z"/>
    <rect x="20" y="19" width="34" height="4" rx="2"/>
    <path d="M24 25 a13 14 0 0 0 26 0 Z" fill="none" stroke="#3a3a3a" stroke-width="3"/>
    <path d="M8 72 q0 -26 29 -28 q29 2 29 28 Z"/>
    <rect x="26" y="50" width="22" height="22" fill="#fff"/>
    <rect x="28" y="52" width="18" height="20"/>
  </svg>
  <h2>Acquisition Consulting</h2>
  <p>Lorem ipsum dolor sit amet, consectetur adipisicing elit, sed do eiusmod tempor incididunt ut labore et dolore magna aliqua. Ut enim ad minim veniam, quis nostrud.</p>
  <a href="#" class="btn">Read More</a>
</article>

<section class="abs testimonials">
  <h2>TESTIMONIALS</h2>
  <div class="abs avatar" role="img" aria-label="Portrait of the client giving the testimonial"></div>
  <div class="abs avatar-pointer"></div>
  <h3>Marissa</h3>
  <p>Lorem ipsum dolor sit amet, consectetur adipisicing elit, sed do eiusmod tempor incididunt ut labore et dolore magna aliqua. Ut enim ad minim veniam, dolore eu fugiat nulla pariatur. Excepteur sint occaecat cupidatat non proident, sunt in culpa te irure dolor in repreh te irure dolor in repreh te irure dolor in repreh qui officia deserunt mollit anim id est laborum...</p>
</section>

<section class="abs lower"></section>
<form class="abs contact-box">
  <h2>Contact Us !</h2>
  <p>Lorem ipsum dolor sit amet, consectetur elit sed do eiusmod tempor incididunt ut labore et dolore magna aliqua. Ut enim ad minim veniam.</p>
  <div class="field first">Name</div>
  <div class="field">E-mail</div>
  <div class="field msg">Massege</div>
  <div class="form-foot"><label><i></i>Lorem ipsum dolor sit amet.</label><a href="#" class="btn">Submit</a></div>
</form>

<h2 class="abs pros-title">QRV Advisors</h2>
<div class="abs pro-photo" style="top:1619px;background:linear-gradient(180deg,#e0855a 0%,#8a5f6a 40%,#5d6e8a 70%,#8c8c8c 100%)" role="img" aria-label="Shipping containers and a truck at a cargo port"></div>
<p class="abs pro-text" style="top:1625px">QRV assists business owners within the logistics industry to implement growth and exit strategies. We offer business planning and merger and acquisition(M&amp;A) advisory services. QRV services are offered by industry executives with extensive M&amp;A experience. Your company will benefit from a unique and outside perspective from consultants that understand your business.</p>
<div class="abs pro-photo" style="top:1771px;background:linear-gradient(180deg,#cfd6de 0%,#8f99a6 50%,#4e5560 100%)" role="img" aria-label="Cargo plane being loaded next to a truck"></div>
<p class="abs pro-text" style="top:1776px">QRV can help you formulate and execute your growth strategy. We take a strategic and consultative approach with our advisory services that will help you grow your business effectively. Since our experience and focus is only in the logistics space, you can be confident that our process will be efficient and streamlined as we help achieve your goals.</p>

<footer class="abs site-footer">
  <div class="abs foot-brand"><div class="brand-name">QRV</div><div class="brand-tag">Mergers &amp; Acquisitions Consulting Services</div></div>
  <p class="abs foot-about">Lorem ipsum dolor sit amet, consectetur adipisicing elit, sed do eiusmod tempor incididunt ut labore et dolore magna aliqua. Ut enim ad minim veniam, quis nostrud exercitation ullamco laboris nisi ut aliquip ex ea commodo consequat.</p>
  <div class="abs foot-col" style="left:489px;top:37px">
    <h4>Site Map</h4>
    <ul><li class="active">Home</li><li>About Us</li><li>Services</li><li>Careers</li><li>Contact Us</li></ul>
  </div>
  <div class="abs foot-col" style="left:661px;top:37px">
    <h4>Get In Touch</h4>
    <div class="foot-contact">www.qrvadvisors-example.com<br>E-mail : info@qrvadvisors-example.com<br>P.O. Box 4820<br>Maple Ridge, IL 60999<br>Call : (555) 014 2290</div>
  </div>
  <div class="abs foot-col" style="left:928px;top:37px">
    <h4>Social Media</h4>
    <div class="foot-social"><span></span><span></span><span></span><span></span><span></span></div>
  </div>
</footer>
<div class="abs copyright">Copyright © 2014 QRV . All Rights Reserved.</div>

</body>
</html>
```